Agriculture Business Card

I want to use my existing logo and use my tagline of "Don't Guess...Soil Test" on the card. Looking for a double sided card that will really get peoples attention.
Contact Info:
Marlow Field Crop Edge
Calvin Brusk
2917 K Lane
Larkin, NE 68593
402-555-0193
calvin.r.brusk@fieldmailbox.net

```html
<!DOCTYPE html>
<html lang="en">
<head>
<meta charset="utf-8">
<title>Marlow Field Crop Edge – Business Card</title>
<link rel="stylesheet" href="https://fonts.googleapis.com/css2?family=Fjalla+One&family=Montserrat:wght@400;600;700&display=swap">
<style>
  :root {
    --backdrop: #232323;
    --card-white: #ffffff;
    --soil-brown: #a3694c;
    --soil-brown-dark: #7c4b34;
    --soil-brown-light: #c98a6b;
    --harvest-yellow: #f5b21c;
    --leaf-green: #3aa84a;
    --leaf-green-light: #7bc143;
    --text-grey: #4a4a4a;
  }
  * { box-sizing: border-box; margin: 0; padding: 0; }
  html, body { width: 1200px; height: 839px; overflow: hidden; }
  body {
    background: var(--backdrop);
    font-family: "Montserrat", sans-serif;
    position: relative;
  }
  .card {
    position: absolute;
    top: 70px;
    width: 400px;
    height: 700px;
    border-radius: 40px;
    overflow: hidden;
  }
  .card--front { left: 170px; background: var(--card-white); }
  .card--back { left: 630px; }

  .brand-name {
    position: absolute;
    top: 150px;
    left: 0; right: 0;
    text-align: center;
    font-family: "Fjalla One", sans-serif;
    font-size: 40px;
    line-height: 1.1;
    color: var(--soil-brown);
  }
  .person-name {
    position: absolute;
    top: 330px;
    left: 0; right: 0;
    text-align: center;
    font-weight: 700;
    font-size: 30px;
    letter-spacing: 1px;
    color: var(--soil-brown);
  }
  .contact-icons {
    position: absolute;
    top: 395px;
    left: 30px; right: 30px;
    display: flex;
    align-items: center;
    gap: 10px;
  }
  .contact-icons .rule {
    flex: 1;
    height: 2px;
    background: var(--leaf-green);
  }
  .icon-tile {
    width: 34px; height: 34px;
    border-radius: 8px;
    background: var(--leaf-green);
    display: flex; align-items: center; justify-content: center;
  }
  .contact-lines {
    position: absolute;
    top: 455px;
    left: 0; right: 0;
    text-align: center;
    font-size: 17px;
    line-height: 1.55;
    color: var(--text-grey);
  }
  .divider-yellow {
    position: absolute;
    top: 530px;
    left: 145px;
    width: 110px;
    height: 2px;
    background: var(--harvest-yellow);
  }
  .address {
    position: absolute;
    top: 550px;
    left: 0; right: 0;
    text-align: center;
    font-size: 17px;
    line-height: 1.55;
    color: var(--text-grey);
  }
  .tagline-band {
    position: absolute;
    left: 0; right: 0; bottom: 0;
    height: 66px;
    background: var(--soil-brown);
    display: flex; align-items: center; justify-content: center;
    color: var(--harvest-yellow);
    font-size: 19px;
    font-weight: 600;
    letter-spacing: 0.5px;
  }

  .back-pattern {
    position: absolute;
    inset: 0;
    background: linear-gradient(160deg, var(--soil-brown-dark) 0%, var(--soil-brown) 50%, var(--soil-brown-light) 100%);
  }
  .back-brand {
    position: absolute;
    top: 50%;
    left: 0; right: 0;
    transform: translateY(-50%);
    text-align: center;
    font-family: "Fjalla One", sans-serif;
    font-size: 26px;
    line-height: 1.1;
    color: var(--harvest-yellow);
  }
</style>
</head>
<body>
  <section class="card card--front">
    <h1 class="brand-name">Marlow Field<br>Crop Edge</h1>
    <p class="person-name">CALVIN BRUSK</p>

    <div class="contact-icons">
      <span class="rule"></span>
      <span class="icon-tile" aria-label="Phone">
        <svg width="18" height="18" viewBox="0 0 24 24"><path fill="#fff" d="M6.6 10.8a15 15 0 0 0 6.6 6.6l2.2-2.2a1 1 0 0 1 1-.25 11.4 11.4 0 0 0 3.6.57 1 1 0 0 1 1 1V20a1 1 0 0 1-1 1A17 17 0 0 1 3 4a1 1 0 0 1 1-1h3.5a1 1 0 0 1 1 1c0 1.25.2 2.45.57 3.57a1 1 0 0 1-.25 1z"/></svg>
      </span>
      <span class="icon-tile" aria-label="Email">
        <svg width="18" height="18" viewBox="0 0 24 24"><rect x="2" y="5" width="20" height="14" rx="2" fill="#fff"/><path d="M3 6l9 7 9-7" fill="none" stroke="#3aa84a" stroke-width="2"/></svg>
      </span>
      <span class="icon-tile" aria-label="Web">
        <svg width="18" height="18" viewBox="0 0 24 24"><circle cx="12" cy="12" r="9" fill="none" stroke="#fff" stroke-width="2"/><ellipse cx="12" cy="12" rx="4" ry="9" fill="none" stroke="#fff" stroke-width="1.6"/><path d="M3 12h18" stroke="#fff" stroke-width="1.6"/></svg>
      </span>
      <span class="rule"></span>
    </div>

    <p class="contact-lines">402-555-0193<br>calvin.r.brusk@fieldmailbox.net</p>
    <span class="divider-yellow"></span>
    <p class="address">2917 K Lane<br>Larkin, NE 68593</p>

    <footer class="tagline-band">Don't Guess...Soil Test</footer>
  </section>

  <section class="card card--back">
    <div class="back-pattern" role="img" aria-label="Repeating embossed brand pattern on brown background"></div>
    <p class="back-brand">Marlow Field<br>Crop Edge</p>
  </section>
</body>
</html>
```